Tree Service Billboard 20x8 ft

We need a billboard design for a tree service company.
The billboard is 20ft x 8 ft so we need a design that is capable to stretching to those dimensions without loosing quality.
I have attached a series of images.
Image 1- Simply a billboard that I think looks good that I would like you to use for inspiration. I am aiming for the same format only no color in the wording, just black white, or gray. I like the the trees in the background, the logo placed to the left, and wording on the right.
Image 2- Current Logo I would like to the left of the billboard
Image 3- Another format of current logo if needed.
Image 4- A drawn out design template
Image 5- Another drawn out design template

Specific things I am looking for
-The contact number to be the largest thing on the design
-The logo on the design
-Key points to the design to say:
Tree Removal
Tree Trimming
Land Development
Stump Grinding
Storm Response
Insured
Free Bids
-The facebook logo
-The Google Logo

```html
<!DOCTYPE html>
<html lang="en">
<head>
<meta charset="utf-8">
<title>Birch Hollow Tree Service Billboard</title>
<link href="https://fonts.googleapis.com/css2?family=Montserrat:wght@800;900&display=swap" rel="stylesheet">
<style>
  :root {
    --page: #e9ebee;
    --forest-dark: #1c2a17;
    --forest-mid: #2f4a22;
    --forest-light: #4b6b2e;
    --ink: #0b0b0b;
    --swoosh-gray: #5a5a5a;
    --white: #ffffff;
    --green: #1f9a3c;
  }
  html, body {
    margin: 0;
    width: 1200px;
    height: 740px;
    overflow: hidden;
    background: var(--page);
  }
  .billboard {
    position: absolute;
    left: 20px;
    top: 50px;
    width: 1160px;
    height: 640px;
    overflow: hidden;
    background: var(--ink);
    font-family: "Montserrat", Arial, sans-serif;
    color: var(--white);
  }
  .forest-backdrop {
    position: absolute;
    inset: 0 0 120px 0;
    background:
      radial-gradient(ellipse at 45% 40%, var(--forest-light) 0%, transparent 55%),
      radial-gradient(ellipse at 80% 30%, var(--forest-mid) 0%, transparent 60%),
      linear-gradient(90deg, var(--forest-dark) 0%, var(--forest-mid) 50%, var(--forest-dark) 100%);
  }
  .wave-band {
    position: absolute;
    inset: 0;
  }
  .service-list {
    position: absolute;
    left: 28px;
    top: 48px;
    margin: 0;
    padding: 0;
    list-style: none;
    font-weight: 900;
    font-size: 52px;
    line-height: 62px;
    text-transform: uppercase;
    text-shadow: 0 3px 6px rgba(0,0,0,0.6);
  }
  .service-list li {
    display: flex;
    align-items: center;
    gap: 10px;
    white-space: nowrap;
  }
  .tick {
    width: 34px;
    height: 34px;
    flex: none;
  }
  .tick-pair { margin-left: 18px; }
  .brand {
    position: absolute;
    right: 70px;
    top: 40px;
    width: 380px;
    text-align: center;
  }
  .brand-ring {
    display: block;
    width: 180px;
    height: 180px;
    margin: 0 auto 28px;
    border: 8px solid var(--white);
    border-radius: 50%;
    box-sizing: border-box;
  }
  .brand-name {
    font-weight: 800;
    font-size: 40px;
    line-height: 46px;
    text-transform: uppercase;
  }
  .contact {
    position: absolute;
    right: 50px;
    bottom: 40px;
    text-align: right;
  }
  .find-us {
    display: flex;
    justify-content: flex-end;
    align-items: center;
    gap: 18px;
    font-weight: 800;
    font-size: 40px;
    text-transform: uppercase;
  }
  .social-dot {
    width: 56px;
    height: 56px;
    border-radius: 50%;
    background: var(--green);
  }
  .phone {
    display: flex;
    align-items: center;
    gap: 14px;
    margin-top: 6px;
    font-weight: 900;
    font-size: 104px;
    line-height: 1;
    letter-spacing: -1px;
  }
  .phone-icon { width: 62px; height: 62px; }
</style>
</head>
<body>
<main class="billboard">
  <div class="forest-backdrop" role="img" aria-label="Photo of a dense green forest canopy"></div>

  <svg class="wave-band" viewBox="0 0 1160 640" preserveAspectRatio="none" aria-hidden="true">
    <path d="M0 520 C 250 560, 520 520, 760 400 C 900 330, 1060 310, 1160 330 L1160 640 L0 640 Z" fill="var(--ink)"/>
    <path d="M640 470 C 820 340, 1000 270, 1160 310 L1160 340 C 1010 300, 840 360, 700 460 Z" fill="var(--swoosh-gray)"/>
    <path d="M0 480 C 120 560, 330 560, 520 520 C 360 580, 140 590, 0 540 Z" fill="var(--white)"/>
  </svg>

  <ul class="service-list">
    <li><svg class="tick" viewBox="0 0 34 34"><circle cx="17" cy="17" r="14" fill="none" stroke="var(--green)" stroke-width="4"/><path d="M10 17 l6 6 l12 -16" fill="none" stroke="var(--green)" stroke-width="5" stroke-linecap="round"/></svg>Tree Removal</li>
    <li><svg class="tick" viewBox="0 0 34 34"><circle cx="17" cy="17" r="14" fill="none" stroke="var(--green)" stroke-width="4"/><path d="M10 17 l6 6 l12 -16" fill="none" stroke="var(--green)" stroke-width="5" stroke-linecap="round"/></svg>Tree Trimming</li>
    <li><svg class="tick" viewBox="0 0 34 34"><circle cx="17" cy="17" r="14" fill="none" stroke="var(--green)" stroke-width="4"/><path d="M10 17 l6 6 l12 -16" fill="none" stroke="var(--green)" stroke-width="5" stroke-linecap="round"/></svg>Land Development</li>
    <li><svg class="tick" viewBox="0 0 34 34"><circle cx="17" cy="17" r="14" fill="none" stroke="var(--green)" stroke-width="4"/><path d="M10 17 l6 6 l12 -16" fill="none" stroke="var(--green)" stroke-width="5" stroke-linecap="round"/></svg>Stump Grinding</li>
    <li><svg class="tick" viewBox="0 0 34 34"><circle cx="17" cy="17" r="14" fill="none" stroke="var(--green)" stroke-width="4"/><path d="M10 17 l6 6 l12 -16" fill="none" stroke="var(--green)" stroke-width="5" stroke-linecap="round"/></svg>Storm Response</li>
    <li><svg class="tick" viewBox="0 0 34 34"><circle cx="17" cy="17" r="14" fill="none" stroke="var(--green)" stroke-width="4"/><path d="M10 17 l6 6 l12 -16" fill="none" stroke="var(--green)" stroke-width="5" stroke-linecap="round"/></svg>Insured<svg class="tick tick-pair" viewBox="0 0 34 34"><circle cx="17" cy="17" r="14" fill="none" stroke="var(--green)" stroke-width="4"/><path d="M10 17 l6 6 l12 -16" fill="none" stroke="var(--green)" stroke-width="5" stroke-linecap="round"/></svg>Free Bids</li>
  </ul>

  <div class="brand">
    <span class="brand-ring"></span>
    <div class="brand-name">Birch Hollow Tree Service</div>
  </div>

  <div class="contact">
    <div class="find-us">Find us on <span class="social-dot"></span><span class="social-dot"></span></div>
    <div class="phone">
      <svg class="phone-icon" viewBox="0 0 24 24" aria-hidden="true"><path d="M6.6 10.8a15.1 15.1 0 0 0 6.6 6.6l2.2-2.2a1 1 0 0 1 1-.25 11.4 11.4 0 0 0 3.6.57 1 1 0 0 1 1 1V20a1 1 0 0 1-1 1A17 17 0 0 1 3 4a1 1 0 0 1 1-1h3.5a1 1 0 0 1 1 1c0 1.25.2 2.45.57 3.57a1 1 0 0 1-.25 1z" fill="var(--green)"/></svg>
      417-555-0148
    </div>
  </div>
</main>
</body>
</html>
```